KTR Photography Editing & Support Services for Real Estate

We require a double sided A4 flyer to promote our photography services to real estate agencies.
This particular service is targeted to rural areas where reliable, professional and highly skilled photographers are difficult to source. We teach the agent how to photograph, they upload files to a server and we take care of the rest (image editing, quality control and delivery). This will give the agents flexibility with when to shoot and eliminates the stress of managing a photographer / contractor. We offer a 1 day face to face training session and competitive packages for equipment start up.
We would like the flyer to look clean & very professional. The flyer should showcase samples of our work to highlight what can be achieved by using our services. We like the look of a black or dark background behind the text and feel that would look nice with our photographs provided. Otherwise open to your suggestions and ideas.
TEXT FOR FLYER:
Welcome to the KTR Real Estate Photography Editing and Support Service
• Take your real estate business to the next level by providing impressive real estate imagery that makes you stands out from the competition
• Omit the stress of trying to find a good photographer or managing an unreliable one and hence have more time to focus on other aspects of your business
• Showcase your listings with better quality and more impactful photographs than your competitors thereby increasing potential for a quick sale
• Great first impressions matter and you will achieve this by looking and feeling more professional. This will attract and retain more future clients.
HOW IT WORKS
• We understand that your time is valuable, so let us handle the editing and delivery of your images. You shoot, and we take care of the rest.
• Images are edited and delivered within 1 working day
INCLUSIONS:
• Full day face to face training (we come to you) and instructional handbook
• We will teach you everything you need to know about your equipment and how to take stunning real estate photographs
• Service turnaround within 1 working day
• Free HELP desk service Mon-Fri
• 12 month Exclusivity (rural towns only) for a limited time
INVESTMENT
• 99 per listing for us to manage images including editing, quality control and delivery (10 Images)
• Ask us about competitive packages for photography equipment if required
SUMMARY
The KTR Real Estate Photography Editing and Support Service is the perfect solution for busy real estate professionals who want to take their business to the next level. Our service is affordable, flexible, and designed to help you showcase your listings in the best possible light.
Contact us today to learn more about how we can help you.

```html
<!DOCTYPE html>
<html lang="en">
<head>
<meta charset="utf-8">
<title>KTR Real Estate Photography Editing and Support Service – Flyer</title>
<link href="https://fonts.googleapis.com/css2?family=Montserrat:wght@300;400;500;600;700&display=swap" rel="stylesheet">
<style>
:root{
  --ink:#2b2b2b;
  --ink-soft:#3a3a3a;
  --paper:#ffffff;
  --mist:#d6d6d6;
  --fog:#c4c4c4;
  --stage:#bdbdbd;
  --text-light:#f2f2f2;
  --text-dark:#1f1f1f;
  --rule:#8a8a8a;
}
*{box-sizing:border-box;margin:0;padding:0}
html,body{width:896px;height:1200px;overflow:hidden}
body{background:var(--stage);font-family:"Montserrat",sans-serif;color:var(--text-light);position:relative}
.page{position:absolute;top:300px;width:424px;height:600px;background:var(--paper);overflow:hidden;box-shadow:0 8px 18px rgba(0,0,0,.35)}
.page--front{left:16px}
.page--back{left:456px}
.abs{position:absolute}
.dark{background:var(--ink)}
.light{background:var(--mist)}
.photo{position:absolute}
/* brand */
.brand{position:absolute;background:linear-gradient(135deg,#fff 0%,#ececec 60%,#fafafa 100%);display:flex;flex-direction:column;align-items:center;justify-content:center}
.brand__name{font-weight:300;font-size:15px;letter-spacing:3.5px;color:#555;white-space:nowrap}
.brand__role{font-weight:300;font-size:7px;letter-spacing:2.4px;color:#555;margin-top:6px}
/* welcome */
.welcome{left:210px;top:121px;width:214px;height:129px;padding:22px 0 0 20px}
.welcome p{font-size:10px;font-weight:500;line-height:1.55}
.welcome strong{font-weight:700;font-size:12.5px}
.welcome__rule{position:absolute;left:20px;top:110px;width:160px;height:1px;background:var(--rule)}
.welcome__rule::before{content:"";position:absolute;left:0;top:-1px;width:46px;height:2px;background:var(--text-light)}
/* section tab */
.tab{position:absolute;padding:2px 8px;font-size:8.5px;font-weight:700;letter-spacing:.3px;white-space:nowrap;border-radius:0 0 3px 3px}
.tab--light{background:var(--paper);color:var(--text-dark);border-radius:3px}
.tab--dark{background:var(--ink);color:var(--text-light)}
/* bullet lists */
.cols{position:absolute;display:flex}
.col{flex:1;padding:0 10px}
.col + .col{border-left:1px solid #777}
.bullets{list-style:none}
.bullets li{position:relative;padding-left:10px;font-size:6.6px;line-height:1.42;margin-bottom:9px}
.bullets li::before{content:"";position:absolute;left:0;top:3px;width:3.5px;height:3.5px;border-radius:50%;background:currentColor}
.on-light{color:var(--text-dark)}
.bullets b{font-weight:700}
/* footer */
.footer{position:absolute;left:0;top:563px;width:424px;height:37px}
.footer svg.bg{position:absolute;inset:0}
.footer__phone{position:absolute;left:24px;top:12px;display:flex;align-items:center;gap:6px;font-size:9.5px;font-weight:600}
.footer__follow{position:absolute;left:130px;top:9px;padding-left:10px;border-left:1px solid #777;height:20px;display:flex;align-items:center;gap:4px;font-size:6px}
.footer__dot{width:10px;height:10px;border-radius:50%;background:var(--text-light)}
.footer__mail{position:absolute;right:32px;top:13px;display:flex;align-items:center;gap:6px;font-size:7px;font-weight:600;color:var(--text-dark)}
/* summary */
.summary{left:0;top:463px;width:424px;height:68px;padding:28px 30px 0;text-align:center;font-size:6.8px;line-height:1.45}
.cta{position:absolute;left:72px;top:540px;width:280px;height:15px;background:var(--fog);border-radius:2px;color:var(--text-dark);font-size:6.8px;text-align:center;line-height:15px}
</style>
</head>
<body>

<!-- FRONT -->
<section class="page page--front">
  <div class="abs dark" style="left:0;top:0;width:168px;height:185px"></div>
  <div class="abs light" style="left:0;top:185px;width:210px;height:94px;background:#e9e9e9"></div>
  <div class="brand" style="left:168px;top:0;width:256px;height:121px;padding-top:6px">
    <div class="brand__name">KIERAN ROWE</div>
    <div class="brand__role">PHOTOGRAPHER</div>
  </div>
  <div class="photo" role="img" aria-label="Modern farmhouse exterior at dusk with stone wall and lit windows" style="left:15px;top:16px;width:195px;height:169px;background:linear-gradient(180deg,#b9b8d0 0%,#d9d1c8 40%,#8f7d68 70%,#e2e2e2 100%)"></div>
  <div class="photo" role="img" aria-label="Black timber cabin on a coastal cliff at sunset" style="left:15px;top:195px;width:185px;height:72px;background:linear-gradient(180deg,#c8b5c0 0%,#e6c7b4 50%,#607a94 75%,#4c5f4a 100%)"></div>
  <div class="abs dark welcome">
    <p>Welcome to<br>the <strong>KTR Real Estate<br>Photography Editing</strong><br>and Support Service</p>
    <div class="welcome__rule"></div>
  </div>
  <div class="abs light" style="left:210px;top:250px;width:214px;height:28px;background:#e2e2e2"></div>

  <div class="abs" style="left:0;top:272px;width:424px;height:1px;background:#555"></div>
  <div class="abs dark" style="left:0;top:278px;width:424px;height:122px"></div>
  <div class="tab tab--light" style="left:170px;top:271px">OUR SERVICE:</div>
  <div class="cols" style="left:10px;top:296px;width:404px">
    <div class="col"><ul class="bullets">
      <li>Take your real estate business to the next level by providing impressive real estate imagery that makes you stands out from the competition.</li>
      <li>Omit the stress of trying to find a good photographer or managing an unreliable one and hence have more time to focus on other aspects of your business.</li>
    </ul></div>
    <div class="col"><ul class="bullets">
      <li>Great first impressions matter and you will achieve this by looking and feeling more professional. This will attract and retain more future clients.</li>
      <li>Showcase your listings with better quality and more impactful photographs than your competitors thereby increasing potential for a quick sale.</li>
    </ul></div>
  </div>

  <div class="photo" role="img" aria-label="Bright bathroom with freestanding bath and arched mirrors" style="left:11px;top:406px;width:126px;height:69px;background:linear-gradient(135deg,#e8e4df,#c9bfb3)"></div>
  <div class="photo" role="img" aria-label="Open-plan kitchen and dining room with timber beams" style="left:149px;top:406px;width:126px;height:69px;background:linear-gradient(135deg,#f0eeea,#a98d72)"></div>
  <div class="photo" role="img" aria-label="Bedroom with large windows overlooking green hills" style="left:287px;top:406px;width:126px;height:69px;background:linear-gradient(135deg,#dedfe0,#8a9a7c)"></div>

  <div class="abs" style="left:0;top:480px;width:424px;height:2px;background:#777"></div>
  <div class="abs light" style="left:0;top:482px;width:424px;height:72px"></div>
  <div class="tab tab--dark" style="left:152px;top:474px;border-radius:3px">HOW IT WORKS</div>
  <div class="cols" style="left:10px;top:502px;width:404px">
    <div class="col" style="border-color:#888"><ul class="bullets on-light">
      <li>We understand that your time is valuable, so let us handle the editing and delivery of your images. You shoot, and we take care of the rest.</li>
    </ul></div>
    <div class="col" style="border-left:1px solid #888;padding-top:9px"><ul class="bullets on-light">
      <li>Images are edited and delivered within 1 working day</li>
    </ul></div>
  </div>

  <footer class="footer">
    <svg class="bg" width="424" height="37" viewBox="0 0 424 37" aria-hidden="true">
      <rect width="424" height="37" fill="#2b2b2b"/>
      <polygon points="242,0 424,0 424,37 205,37" fill="#dcdcdc"/>
      <polygon points="256,6 424,6 424,37 222,37" fill="#fff"/>
    </svg>
    <div class="footer__phone"><svg width="10" height="10" viewBox="0 0 24 24" aria-hidden="true"><path d="M6.6 10.8a15 15 0 0 0 6.6 6.6l2.2-2.2a1 1 0 0 1 1-.25 11.4 11.4 0 0 0 3.6.6 1 1 0 0 1 1 1V20a1 1 0 0 1-1 1A17 17 0 0 1 3 4a1 1 0 0 1 1-1h3.5a1 1 0 0 1 1 1c0 1.25.2 2.45.6 3.6a1 1 0 0 1-.25 1z" fill="none" stroke="#f2f2f2" stroke-width="2"/></svg>61 400 555 019</div>
    <div class="footer__follow">Follow us: <span class="footer__dot"></span></div>
    <div class="footer__mail"><svg width="11" height="8" viewBox="0 0 11 8" aria-hidden="true"><rect width="11" height="8" fill="#1f1f1f"/><path d="M0.5 0.5 5.5 4.5 10.5 0.5" fill="none" stroke="#fff" stroke-width="1"/></svg>shoot@kieranrowe.com.au</div>
  </footer>
</section>

<!-- BACK -->
<section class="page page--back">
  <div class="abs dark" style="left:0;top:0;width:212px;height:247px"></div>
  <div class="brand" style="left:212px;top:0;width:212px;height:98px">
    <div class="brand__name" style="font-size:13px;letter-spacing:3px">KIERAN ROWE</div>
    <div class="brand__role">PHOTOGRAPHER</div>
  </div>
  <div class="tab tab--light" style="left:16px;top:17px;padding:3px 14px">INCLUSIONS:</div>
  <ul class="bullets" style="position:absolute;left:22px;top:52px;width:180px">
    <li style="margin-bottom:14px;width:180px">Full day face to face training (we come to you) and instructional handbook</li>
    <li style="margin-bottom:11px;width:128px">We will teach you everything you need to know about your equipment and how to take stunning real estate photographs</li>
    <li style="margin-bottom:11px;width:128px">Service turnaround within 1 working day</li>
    <li style="margin-bottom:11px;width:128px">Free HELP desk service <b>Mon-Fri</b></li>
    <li style="width:100px">12 month Exclusivity (rural towns only) for a limited time</li>
  </ul>
  <div class="photo" role="img" aria-label="Timber-lined living room with tall windows, hanging fireplace and mountain view at dusk" style="left:165px;top:98px;width:259px;height:149px;background:linear-gradient(180deg,#9a7552 0%,#2f4a6e 35%,#6b84a0 55%,#5a4a3c 80%,#8c8884 100%)"></div>

  <div class="abs" style="left:0;top:251px;width:424px;height:2px;background:#666"></div>
  <div class="abs dark" style="left:0;top:256px;width:424px;height:75px"></div>
  <div class="tab tab--light" style="left:168px;top:249px;padding:3px 14px">INVESTMENT</div>
  <div class="cols" style="left:25px;top:284px;width:380px">
    <div class="col"><ul class="bullets"><li>99 per listing for us to manage images including editing, quality control and delivery (10 Images)</li></ul></div>
    <div class="col" style="padding-left:16px"><ul class="bullets"><li>Ask us about competitive packages for photography equipment if required</li></ul></div>
  </div>

  <div class="abs light" style="left:0;top:332px;width:424px;height:122px;background:#e3e3e3"></div>
  <div class="photo" role="img" aria-label="Dark living room with black sofa and cushions" style="left:12px;top:351px;width:124px;height:94px;background:linear-gradient(135deg,#5c6066,#2a2c30)"></div>
  <div class="photo" role="img" aria-label="Dark weatherboard cottage with lit porch and garden path at dusk" style="left:150px;top:351px;width:124px;height:94px;background:linear-gradient(180deg,#8ea3bf 0%,#3a3d42 55%,#5f7a3c 100%)"></div>
  <div class="photo" role="img" aria-label="Hallway with framed pictures, bench and timber floor" style="left:288px;top:351px;width:124px;height:94px;background:linear-gradient(135deg,#efece6,#9c7a58)"></div>

  <div class="abs" style="left:0;top:458px;width:424px;height:2px;background:#666"></div>
  <div class="abs dark summary">The KTR Real Estate Photography Editing and Support Service is the perfect solution for busy real estate professionals who want to take their business to the next level. Our service is affordable, flexible, and designed to help you showcase your listings in the best possible light.</div>
  <div class="tab tab--light" style="left:168px;top:456px;padding:3px 18px">SUMMARY</div>
  <div class="cta">Contact us today to learn more about how we can help you.</div>

  <footer class="footer">
    <svg class="bg" width="424" height="37" viewBox="0 0 424 37" aria-hidden="true">
      <rect width="424" height="37" fill="#2b2b2b"/>
      <polygon points="242,0 424,0 424,37 205,37" fill="#dcdcdc"/>
      <polygon points="256,6 424,6 424,37 222,37" fill="#fff"/>
    </svg>
    <div class="footer__phone"><svg width="10" height="10" viewBox="0 0 24 24" aria-hidden="true"><path d="M6.6 10.8a15 15 0 0 0 6.6 6.6l2.2-2.2a1 1 0 0 1 1-.25 11.4 11.4 0 0 0 3.6.6 1 1 0 0 1 1 1V20a1 1 0 0 1-1 1A17 17 0 0 1 3 4a1 1 0 0 1 1-1h3.5a1 1 0 0 1 1 1c0 1.25.2 2.45.6 3.6a1 1 0 0 1-.25 1z" fill="none" stroke="#f2f2f2" stroke-width="2"/></svg>61 400 555 019</div>
    <div class="footer__follow">Follow us: <span class="footer__dot"></span></div>
    <div class="footer__mail"><svg width="11" height="8" viewBox="0 0 11 8" aria-hidden="true"><rect width="11" height="8" fill="#1f1f1f"/><path d="M0.5 0.5 5.5 4.5 10.5 0.5" fill="none" stroke="#fff" stroke-width="1"/></svg>shoot@kieranrowe.com.au</div>
  </footer>
</section>

</body>
</html>
```